Business Card and Simple Logo Desgin

New Zealand based start up company "Vesta Advisory LTD" requires business cards and simple logo design.

Card Content.

Vesta Advisory LTD

Rebecca Thornbury
CA, BMS (Hons)

r.thornbury@vestaadvisory.co.nz
PH +64 21 574 613

Target Market(s)

Corporate Business in IT, Finance and accounting.

Industry/Entity Type

Business

```html
<!DOCTYPE html>
<html lang="en">
<head>
<meta charset="utf-8">
<title>Vesta Advisory Ltd – Business Card</title>
<link href="https://fonts.googleapis.com/css2?family=Source+Sans+3:wght@400;600;700&display=swap" rel="stylesheet">
<style>
  :root {
    --brand-blue: #0033ff;
    --brand-orange: #ff6600;
    --brand-green: #66bb00;
    --ink: #333333;
    --paper: #ffffff;
    --edge: #7a7a7a;
  }
  html, body {
    margin: 0;
    padding: 0;
    width: 1200px;
    height: 695px;
    overflow: hidden;
    background: var(--paper);
  }
  .card {
    position: relative;
    width: 1200px;
    height: 695px;
    box-sizing: border-box;
    border: 2px solid var(--edge);
    background: var(--paper);
    font-family: "Source Sans 3", sans-serif;
    color: var(--ink);
    overflow: hidden;
  }
  .brand {
    position: absolute;
    left: 92px;
    top: 90px;
    display: flex;
    align-items: center;
    gap: 26px;
  }
  .brand-mark {
    width: 110px;
    height: 110px;
    border-radius: 50%;
    background: var(--brand-blue);
    flex: none;
  }
  .brand-name {
    margin: 0;
    font-size: 58px;
    font-weight: 700;
    color: var(--brand-blue);
    letter-spacing: -0.5px;
    line-height: 1;
  }
  .holder {
    position: absolute;
    left: 90px;
    top: 340px;
    margin: 0;
  }
  .holder-name {
    margin: 0;
    font-size: 32px;
    font-weight: 700;
    line-height: 1;
  }
  .holder-credentials {
    margin: 26px 0 0;
    font-size: 29px;
    font-weight: 400;
    line-height: 1;
  }
  .contact {
    position: absolute;
    left: 90px;
    top: 523px;
    margin: 0;
    font-size: 30px;
    font-weight: 400;
    font-style: normal;
    line-height: 1;
  }
  .contact p { margin: 0; }
  .contact p + p { margin-top: 36px; }
  .side-stripe {
    position: absolute;
    top: 0;
    left: 1124px;
    width: 23px;
    height: 100%;
    display: flex;
    flex-direction: column;
  }
  .side-stripe span { flex: 1; }
  .stripe-blue { background: var(--brand-blue); }
  .stripe-orange { background: var(--brand-orange); }
  .stripe-green { background: var(--brand-green); }
</style>
</head>
<body>
  <main class="card">
    <header class="brand">
      <div class="brand-mark" aria-hidden="true"></div>
      <h1 class="brand-name">Vesta Advisory Ltd</h1>
    </header>

    <section class="holder">
      <h2 class="holder-name">Rebecca Thornbury</h2>
      <p class="holder-credentials">CA, BMS (Hons)</p>
    </section>

    <address class="contact">
      <p>r.thornbury@vestaadvisory.co.nz</p>
      <p>PH +64 21 574 613</p>
    </address>

    <div class="side-stripe" aria-hidden="true">
      <span class="stripe-blue"></span>
      <span class="stripe-orange"></span>
      <span class="stripe-green"></span>
    </div>
  </main>
</body>
</html>
```